graphic showing our process of education as a process called a pipeline

Also see my updated comments on discussion section.
Title of the graphic needs to be:
TITLE = The KESIMA Strategic Leadership Pipeline = larger, bold heading
SUB-TITLE = Developing a steady flow of servant leaders for Tanzania's future = under title; smaller font
change the text for each of the 7 steps to match the outcomes listed on the newly attached PDF (strategic pipeline 11x17)
Pipe should be straight or mostly straight.
Pipe should not be in a strong or dark color.
Any icons or symbols should be simple and professional, not like cartoon or childish.
We need a graphic design that shows our PROCESS, called a "pipeline," that is creating future leaders. We are a US-based non-profit that operates a Christian school in rural Tanzania for 600 students (pre-K through 12th grade). It starts with child sponsorship program that allows poor children and orphans to attend school, we have a primary school (like USA elementary school, pre-K thru 7th), and are building a secondary boarding school (like USA middle and high school, grades 8-12), where students will live on campus in dormitories. We offer education, scholarships, leadership development experiences, help finding and securing college scholarships, academic and career counseling, placements for internships and jobs, and networking and leadership development content and events to create the next generation of servant leaders for the country. Prominent colors should probably be the green, blue and black in the Tanzania flag; we want the design to communicate "smart" and "strategic." The stages of the pipeline need to be properly named; we need to show a "leak" in the pipeline after the primary school because we currently have to send our students AWAY to other boarding schools because we don't have one. As the attached recording says, this is bad for their progress. The attached pipeline graphic is very rough and NOT meant to be imitated. It is factually correct, but is busy and not attractive.

Target Market(s)

Major financial contributors and foundations that want to give money to the cause

Industry/Entity Type

non-profit/Christian ministry in education

Font styles to use
Sans Serif

Requirements
Must have
• A "smart" and strategic" feel; preferably visible when on a half page
Nice to have
• a smart, sophisticated, serious look and feel
Should not have
• an elementary school feel

```html
<!DOCTYPE html>
<html lang="en">
<head>
<meta charset="UTF-8">
<title>The KESIMA Strategic Leadership Pipeline</title>
<link href="https://fonts.googleapis.com/css2?family=DM+Sans:wght@400;500;700;800&display=swap" rel="stylesheet">
<style>
  :root {
    --page-bg: #e6e7ec;
    --card-bg: #ffffff;
    --green: #3db54a;
    --blue: #1ea0dc;
    --heading: #2a2a2a;
    --body: #6b6b6b;
    --accent-line: #f2c94c;
    --flag-yellow: #f2d230;
    --flag-black: #151515;
  }
  * { margin: 0; padding: 0; box-sizing: border-box; }
  html, body { width: 1200px; height: 776px; overflow: hidden; background: var(--page-bg); }
  body { font-family: "DM Sans", Arial, sans-serif; position: relative; }

  .card {
    position: absolute; left: 16px; top: 33px; width: 1168px; height: 712px;
    background: var(--card-bg); border-radius: 48px; overflow: hidden;
  }
  .header {
    height: 126px;
    background: linear-gradient(90deg, var(--green) 0%, var(--blue) 100%);
    text-align: center; color: #fff; padding-top: 28px;
  }
  .title { font-size: 47px; font-weight: 700; letter-spacing: -0.3px; line-height: 1; }
  .subtitle { font-size: 18px; font-weight: 600; margin-top: 12px; }

  .graphics { position: absolute; left: 0; top: 0; width: 1200px; height: 776px; }

  .stage { position: absolute; width: 250px; }
  .stage-name { font-size: 20.5px; font-weight: 700; color: var(--heading); line-height: 1.18; }
  .stage-text { font-size: 14.5px; color: var(--body); line-height: 1.32; margin-top: 16px; }

  .stage-icon {
    display: block; width: 30px; height: 30px; border-radius: 6px;
    background: #bfe3f5; margin-bottom: 12px;
  }
  .stage-icon.wide { width: 48px; }

  .brand {
    position: absolute; left: 958px; top: 418px;
    display: flex; align-items: center; gap: 10px;
    font-size: 44px; font-weight: 800; color: var(--blue); letter-spacing: 0.5px; line-height: 1;
  }
  .brand-dot { width: 14px; height: 14px; border-radius: 50%; background: var(--green); }
</style>
</head>
<body>
  <div class="card">
    <header class="header">
      <h1 class="title">The KESIMA Strategic Leadership Pipeline</h1>
      <p class="subtitle">Developing a steady flow of servant leaders for Tanzania's future</p>
    </header>
  </div>

  <svg class="graphics" viewBox="0 0 1200 776" aria-hidden="true">
    <defs>
      <linearGradient id="pipeFlow" gradientUnits="userSpaceOnUse" x1="43" y1="0" x2="946" y2="0">
        <stop offset="0" stop-color="#27a7e1"/>
        <stop offset="0.45" stop-color="#2fb0a0"/>
        <stop offset="1" stop-color="#3db54a"/>
      </linearGradient>
      <clipPath id="cardShape"><rect x="16" y="33" width="1168" height="712" rx="48"/></clipPath>
    </defs>

    <!-- guide lines -->
    <g stroke="var(--accent-line)" stroke-width="2">
      <line x1="49" y1="264" x2="49" y2="385"/>
      <line x1="340" y1="228" x2="340" y2="385"/>
      <line x1="640" y1="264" x2="640" y2="385"/>
      <line x1="941" y1="200" x2="941" y2="385"/>
      <line x1="181" y1="500" x2="181" y2="696"/>
      <line x1="485" y1="506" x2="485" y2="676"/>
      <line x1="790" y1="506" x2="790" y2="694"/>
    </g>
    <g fill="var(--green)">
      <circle cx="49" cy="398" r="3.5"/><circle cx="340" cy="398" r="3.5"/>
      <circle cx="640" cy="398" r="3.5"/><circle cx="941" cy="398" r="3.5"/>
      <circle cx="181" cy="484" r="3.5"/><circle cx="485" cy="484" r="3.5"/>
      <circle cx="790" cy="484" r="3.5"/>
    </g>

    <!-- pipe -->
    <path d="M43 441 H352 C378 441 368 408 396 408 H420 C448 408 438 441 464 441 H946"
          fill="none" stroke="url(#pipeFlow)" stroke-width="34"/>
    <path d="M43 446 H352 C378 446 368 413 396 413 H420 C448 413 438 446 464 446 H946"
          fill="none" stroke="#ffffff" stroke-width="5"/>
    <g fill="url(#pipeFlow)">
      <rect x="42" y="420" width="14" height="44"/>
      <rect x="174" y="420" width="14" height="44"/>
      <rect x="333" y="420" width="14" height="44"/>
      <rect x="478" y="420" width="14" height="44"/>
      <rect x="633" y="420" width="14" height="44"/>
      <rect x="783" y="420" width="14" height="44"/>
      <rect x="934" y="420" width="14" height="44"/>
    </g>
    <g fill="#ffffff">
      <rect x="46" y="442" width="6" height="8"/><rect x="178" y="442" width="6" height="8"/>
      <rect x="337" y="442" width="6" height="8"/><rect x="482" y="442" width="6" height="8"/>
      <rect x="637" y="442" width="6" height="8"/><rect x="787" y="442" width="6" height="8"/>
      <rect x="938" y="442" width="6" height="8"/>
    </g>

    <!-- leak -->
    <g fill="#27a7e1">
      <path d="M340 472 C342 477 344 479 344 482 A4 4 0 0 1 336 482 C336 479 338 477 340 472 Z"/>
      <path d="M340 490 C345 499 349 503 349 509 A9 9 0 0 1 331 509 C331 503 335 499 340 490 Z"/>
      <path d="M340 521 C342 526 344 528 344 531 A4 4 0 0 1 336 531 C336 528 338 526 340 521 Z"/>
      <path d="M340 538 C341 541 342 542 342 544 A2 2 0 0 1 338 544 C338 542 339 541 340 538 Z"/>
    </g>

    <!-- flag band corner -->
    <g clip-path="url(#cardShape)">
      <polygon points="1040,760 1200,650 1200,676 1078,760" fill="var(--flag-yellow)"/>
      <polygon points="1052,760 1200,658 1200,690 1098,760" fill="var(--flag-black)"/>
    </g>
  </svg>

  <section class="stage" style="left:65px; top:263px;">
    <h2 class="stage-name">KESIMA<br>Sponsorship<br>Program</h2>
    <p class="stage-text">Close early<br>development gap.</p>
  </section>

  <section class="stage" style="left:196px; top:545px;">
    <span class="stage-icon" role="img" aria-label="Icon of a student reading"></span>
    <h2 class="stage-name">KESIMA<br>Primary School</h2>
    <p class="stage-text">Potential leaders with<br>Biblical worldview &amp; strong<br>academic foundations.</p>
  </section>

  <section class="stage" style="left:355px; top:227px;">
    <h2 class="stage-name">KESIMA<br>Secondary School</h2>
    <p class="stage-text">Emerging leaders with<br>concrete skills and strong<br>servant mindset.</p>
  </section>

  <section class="stage" style="left:502px; top:526px;">
    <h2 class="stage-name">KESIMA Service<br>Leadership<br>Experience</h2>
    <p class="stage-text">Growing servant leaders<br>with practical<br>experience to effect<br>change for the Kingdom.</p>
  </section>

  <section class="stage" style="left:657px; top:263px;">
    <h2 class="stage-name">KESIMA Higher<br>Education Support</h2>
    <p class="stage-text">Expanding vision, capability,<br>&amp; motivation to solve bigger<br>challenges for the nation.</p>
  </section>

  <section class="stage" style="left:806px; top:546px;">
    <h2 class="stage-name">KESIMA<br>Employment<br>Center</h2>
    <p class="stage-text">Capable Christ-centered<br>leaders in the marketplace,<br>as value adding employees<br>and entrepreneurs.</p>
  </section>

  <section class="stage" style="left:958px; top:199px;">
    <span class="stage-icon wide" role="img" aria-label="Icon of a group of leaders"></span>
    <h2 class="stage-name">KESIMA<br>Leadership Hub</h2>
    <p class="stage-text">Mature Christian leaders<br>being placed &amp; positioned<br>for leadership roles in the<br>community &amp; nation.</p>
  </section>

  <div class="brand"><span>KESIMA</span><span class="brand-dot"></span></div>
</body>
</html>
```